Banner Ad for Weight Loss Product Site

We need a banner ad design for a new company selling a weight loss online programme (Ebook). The product is called "Your FitRoute" and is suitable for people that want to lose weight fast and without doing sports, regardless of age. We would like to see designs that are eye-catching and at its best animated like in the example files. The final design should exhibit a professional look that encourages the customers to buy our product. The text should be "Persönlicher Diätplan zum Abnehmen?" as a title and "Jetzt informieren" for the button field. Thank you!

Industry/Entity Type

Weight

```html
<!DOCTYPE html>
<html lang="de">
<head>
<meta charset="utf-8">
<title>Your FitRoute – Banner Set</title>
<link rel="stylesheet" href="https://fonts.googleapis.com/css2?family=Arimo:wght@400;700&display=swap">
<style>
  :root {
    --stage: #d8bd98;
    --green-dark: #3a7419;
    --green-mid: #4d8c24;
    --green-light: #6aa834;
    --orange: #f5a623;
    --orange-dark: #e58a0c;
    --button-text: #1d1d1d;
    --arrow: #4b8a22;
    --white: #ffffff;
    --photo-skin: #c99a7c;
    --photo-hair: #5a3a28;
    --photo-top: #2a2a2a;
    --product-light: #e9efe2;
    --product-green: #8bbf5a;
  }
  * { box-sizing: border-box; margin: 0; padding: 0; }
  html, body { width: 1200px; height: 900px; overflow: hidden; }
  body {
    background: var(--stage);
    font-family: "Arimo", Arial, sans-serif;
    position: relative;
  }

  .banner {
    position: absolute;
    overflow: hidden;
    background: var(--green-dark);
  }
  .banner::before {
    content: "";
    position: absolute;
    width: 160%;
    height: 150%;
    left: -70%;
    top: -20%;
    border-radius: 50%;
    background: var(--green-mid);
  }
  .banner::after {
    content: "";
    position: absolute;
    width: 120%;
    height: 120%;
    left: -75%;
    top: -10%;
    border-radius: 50%;
    background: var(--green-light);
    opacity: .55;
  }
  .banner > * { position: absolute; z-index: 1; }
  .banner > .headline { z-index: 2; }

  .headline {
    color: var(--white);
    font-weight: 700;
    text-transform: uppercase;
    text-align: center;
    white-space: nowrap;
    text-shadow: 0 1px 2px rgba(0,0,0,.35);
  }
  .headline span { position: absolute; left: 0; right: 0; }

  .cta {
    display: flex;
    align-items: center;
    justify-content: space-between;
    background: linear-gradient(var(--orange), var(--orange-dark));
    border-radius: 999px;
    color: var(--button-text);
    font-weight: 700;
    white-space: nowrap;
    box-shadow: 0 1px 3px rgba(0,0,0,.35);
  }
  .cta svg { flex: none; }

  .brand {
    border-radius: 50%;
    background: var(--green-mid);
    border: 3px solid var(--white);
    display: flex;
    align-items: center;
    justify-content: center;
    text-align: center;
    color: var(--white);
    font-weight: 700;
    line-height: 1.05;
  }

  .model-photo {
    background: linear-gradient(180deg, var(--photo-hair) 0%, var(--photo-skin) 35%, var(--photo-top) 62%, var(--photo-skin) 80%, var(--photo-top) 100%);
    opacity: .9;
  }
  .product-shot {
    background: linear-gradient(160deg, var(--product-light) 0%, var(--white) 45%, var(--product-green) 100%);
    border-radius: 4px;
    opacity: .92;
  }

  /* Leaderboard */
  .leaderboard { left: 125px; top: 18px; width: 851px; height: 104px; }
  .leaderboard .model-photo { left: 10px; top: 0; width: 180px; height: 104px; }
  .leaderboard .product-shot { left: 222px; top: 8px; width: 78px; height: 90px; }
  .leaderboard .headline { left: 306px; width: 240px; top: 0; height: 104px; font-size: 18px; }
  .leaderboard .headline span:nth-child(1) { top: 18px; }
  .leaderboard .headline span:nth-child(2) { top: 58px; }
  .leaderboard .cta { left: 590px; top: 41px; width: 144px; height: 35px; padding: 0 10px 0 12px; font-size: 13px; }
  .leaderboard .brand { left: 753px; top: 6px; width: 94px; height: 94px; font-size: 14px; }

  /* Small horizontal */
  .strip { left: 125px; top: 143px; width: 546px; height: 70px; }
  .strip .model-photo { left: 6px; top: 0; width: 100px; height: 70px; }
  .strip .product-shot { left: 140px; top: 4px; width: 52px; height: 62px; }
  .strip .headline { left: 196px; width: 180px; top: 0; height: 70px; font-size: 12px; }
  .strip .headline span:nth-child(1) { top: 12px; }
  .strip .headline span:nth-child(2) { top: 40px; }
  .strip .cta { left: 379px; top: 28px; width: 92px; height: 23px; padding: 0 5px 0 7px; font-size: 9px; }
  .strip .brand { left: 475px; top: 3px; width: 64px; height: 64px; font-size: 10px; border-width: 2px; }

  /* Large square */
  .square-large { left: 200px; top: 237px; width: 394px; height: 327px; }
  .square-large .headline { left: 0; width: 394px; top: 0; font-size: 26px; }
  .square-large .headline span:nth-child(1) { top: 10px; padding-left: 30px; }
  .square-large .headline span:nth-child(2) { top: 52px; }
  .square-large .model-photo { left: 4px; top: 90px; width: 153px; height: 237px; }
  .square-large .cta { left: 186px; top: 105px; width: 190px; height: 40px; padding: 0 12px 0 16px; font-size: 17px; }
  .square-large .product-shot { left: 160px; top: 155px; width: 120px; height: 159px; }
  .square-large .brand { left: 284px; top: 172px; width: 98px; height: 98px; font-size: 15px; }

  /* Medium square */
  .square-medium { left: 221px; top: 588px; width: 352px; height: 292px; }
  .square-medium .headline { left: 0; width: 352px; top: 0; font-size: 22px; }
  .square-medium .headline span:nth-child(1) { top: 11px; padding-left: 30px; }
  .square-medium .headline span:nth-child(2) { top: 48px; padding-left: 22px; }
  .square-medium .model-photo { left: 4px; top: 80px; width: 126px; height: 212px; }
  .square-medium .cta { left: 165px; top: 94px; width: 170px; height: 35px; padding: 0 10px 0 14px; font-size: 15px; }
  .square-medium .product-shot { left: 134px; top: 139px; width: 112px; height: 146px; }
  .square-medium .brand { left: 255px; top: 150px; width: 92px; height: 92px; font-size: 14px; }

  /* Skyscrapers */
  .sky-narrow { left: 704px; top: 178px; width: 141px; height: 702px; }
  .sky-wide { left: 882px; top: 178px; width: 188px; height: 702px; }
  .sky-narrow .brand { left: 23px; top: 21px; width: 94px; height: 94px; font-size: 14px; }
  .sky-wide .brand { left: 45px; top: 10px; width: 98px; height: 98px; font-size: 15px; }
  .sky-narrow .headline, .sky-wide .headline { left: 0; right: 0; top: 128px; }
  .sky-narrow .headline { font-size: 15px; }
  .sky-wide .headline { font-size: 20px; }
  .sky-narrow .headline span:nth-child(1), .sky-wide .headline span:nth-child(1) { top: 0; }
  .sky-narrow .headline span:nth-child(2), .sky-wide .headline span:nth-child(2) { top: 42px; }
  .sky-narrow .headline span:nth-child(3), .sky-wide .headline span:nth-child(3) { top: 84px; }
  .sky-narrow .cta { left: 5px; top: 255px; width: 131px; height: 39px; padding: 0 8px 0 10px; font-size: 12px; }
  .sky-wide .cta { left: 8px; top: 255px; width: 174px; height: 40px; padding: 0 12px 0 16px; font-size: 16px; }
  .sky-narrow .product-shot { left: 10px; top: 326px; width: 121px; height: 146px; }
  .sky-wide .product-shot { left: 12px; top: 314px; width: 164px; height: 158px; }
  .sky-narrow .model-photo { left: 0; top: 472px; width: 141px; height: 230px; }
  .sky-wide .model-photo { left: 0; top: 472px; width: 188px; height: 230px; }
</style>
</head>
<body>

  <section class="banner leaderboard" aria-label="Banner 851 × 104">
    <div class="model-photo" role="img" aria-label="Lächelnde Frau in Sporttop zeigt auf den Betrachter"></div>
    <div class="product-shot" role="img" aria-label="Ebook-Cover mit Diätplan und DVDs"></div>
    <h2 class="headline"><span>Persönlicher Diätplan</span><span>zum Abnehmen?</span></h2>
    <div class="cta">Jetzt informieren
      <svg width="9" height="11" viewBox="0 0 9 11"><path d="M0 0 L9 5.5 L0 11Z" fill="var(--arrow)"/></svg>
    </div>
    <div class="brand">Your<br>FitRoute</div>
  </section>

  <section class="banner strip" aria-label="Banner 546 × 70">
    <div class="model-photo" role="img" aria-label="Lächelnde Frau in Sporttop zeigt auf den Betrachter"></div>
    <div class="product-shot" role="img" aria-label="Ebook-Cover mit Diätplan und DVDs"></div>
    <h2 class="headline"><span>Persönlicher Diätplan</span><span>zum Abnehmen?</span></h2>
    <div class="cta">Jetzt informieren
      <svg width="6" height="8" viewBox="0 0 9 11"><path d="M0 0 L9 5.5 L0 11Z" fill="var(--arrow)"/></svg>
    </div>
    <div class="brand">Your<br>FitRoute</div>
  </section>

  <section class="banner square-large" aria-label="Banner 394 × 327">
    <h2 class="headline"><span>Persönlicher Diätplan</span><span>zum Abnehmen?</span></h2>
    <div class="model-photo" role="img" aria-label="Schlanke Frau in Sportkleidung mit Maßband um die Taille"></div>
    <div class="cta">Jetzt informieren
      <svg width="11" height="14" viewBox="0 0 9 11"><path d="M0 0 L9 5.5 L0 11Z" fill="var(--arrow)"/></svg>
    </div>
    <div class="product-shot" role="img" aria-label="Ebook-Cover mit Diätplan, DVDs und aufgeschlagener Broschüre"></div>
    <div class="brand">Your<br>FitRoute</div>
  </section>

  <section class="banner square-medium" aria-label="Banner 352 × 292">
    <h2 class="headline"><span>Persönlicher Diätplan</span><span>zum Abnehmen?</span></h2>
    <div class="model-photo" role="img" aria-label="Schlanke Frau in Sportkleidung mit Maßband um die Taille"></div>
    <div class="cta">Jetzt informieren
      <svg width="10" height="12" viewBox="0 0 9 11"><path d="M0 0 L9 5.5 L0 11Z" fill="var(--arrow)"/></svg>
    </div>
    <div class="product-shot" role="img" aria-label="Ebook-Cover mit Diätplan, DVDs und aufgeschlagener Broschüre"></div>
    <div class="brand">Your<br>FitRoute</div>
  </section>

  <section class="banner sky-narrow" aria-label="Banner 141 × 702">
    <div class="brand">Your<br>FitRoute</div>
    <h2 class="headline"><span>Persönlicher</span><span>Diätplan</span><span>zum Abnehmen?</span></h2>
    <div class="cta">Jetzt informieren
      <svg width="8" height="10" viewBox="0 0 9 11"><path d="M0 0 L9 5.5 L0 11Z" fill="var(--arrow)"/></svg>
    </div>
    <div class="product-shot" role="img" aria-label="Ebook-Cover mit Diätplan, DVDs und aufgeschlagener Broschüre"></div>
    <div class="model-photo" role="img" aria-label="Lächelnde Frau in Sporttop zeigt auf den Betrachter"></div>
  </section>

  <section class="banner sky-wide" aria-label="Banner 188 × 702">
    <div class="brand">Your<br>FitRoute</div>
    <h2 class="headline"><span>Persönlicher</span><span>Diätplan</span><span>zum Abnehmen?</span></h2>
    <div class="cta">Jetzt informieren
      <svg width="10" height="13" viewBox="0 0 9 11"><path d="M0 0 L9 5.5 L0 11Z" fill="var(--arrow)"/></svg>
    </div>
    <div class="product-shot" role="img" aria-label="Ebook-Cover mit Diätplan, DVDs und aufgeschlagener Broschüre"></div>
    <div class="model-photo" role="img" aria-label="Lächelnde Frau in Sporttop zeigt auf den Betrachter"></div>
  </section>

</body>
</html>
```